Very visible CoWorking Building Sign overlooking downtown LA and 110 freeway

Our building is drab but very visible and in the best location. We need a great sign for our monolith that overlooks downtown LA and the 100 freeway. We are a new CoWorking business and would like to have a few things we do on the sign: private offices, virtual offices, CoWorking Lounge. Everything we have seen is ho-hum. Can you get us noticed? We need people to know what we do and that we are here but in a creative, professional, unique sign.
Target Market(s)
People who have a business in DTLA, remote workers and those who work from home who need a professional address.
Requirements
Must have
- Our logo (which can be somewhat reimagined) which has our address 2417 on it. The three things we focus on: Private Offices, Virtual Offices, CoWorking Lounge. Incorporate some Navy. Readable from several hundred feet away.
Nice to have
- Mural feel? Something inspirational in this crazy COVID times? Graphics? Color block. I like the idea of decorative but it has to be readable as a building sign. The same with the use of colors. Our colors are grays and navy but with a pop of the chartreuse (we have 2 velvet chartreuse chairs in the space). Helpful to view our website: Harborview2417.com.
Should not have
- Not too graffiti. Keep it professional but unique and wow.

```html
<!DOCTYPE html>
<html lang="en">
<head>
<meta charset="utf-8">
<title>2417 Harborview – Building Sign</title>
<link href="https://fonts.googleapis.com/css2?family=Tinos:wght@400;700&display=swap" rel="stylesheet">
<style>
  :root {
    --navy: #0f2a4f;
    --royal: #1467b8;
    --lime: #8dc63f;
    --white: #ffffff;
    --backdrop: #d4d6d9;
  }
  html, body {
    margin: 0;
    padding: 0;
    width: 834px;
    height: 1200px;
    overflow: hidden;
    background: var(--backdrop);
  }
  .canvas {
    position: relative;
    width: 834px;
    height: 1200px;
  }
  .sign {
    position: absolute;
    left: 0;
    top: 287px;
    width: 834px;
    height: 625px;
    background: var(--navy);
    overflow: hidden;
    font-family: "Tinos", "Times New Roman", serif;
  }
  .sign__waves {
    position: absolute;
    inset: 0;
  }
  .service {
    position: absolute;
    top: 34px;
    width: 240px;
    text-align: center;
  }
  .service__icon {
    display: block;
    width: 192px;
    height: 192px;
    margin: 0 auto;
    border-radius: 50%;
    background: var(--lime);
    box-shadow: 0 0 0 3px var(--white);
  }
  .service__label {
    margin: 22px 0 0;
    color: var(--white);
    font-weight: 700;
    font-size: 33px;
    line-height: 37px;
    letter-spacing: 0.5px;
  }
  .service--private { left: 49px; }
  .service--virtual { left: 287px; }
  .service--lounge  { left: 522px; }
  .divider {
    position: absolute;
    top: 50px;
    width: 2px;
    height: 190px;
    background: var(--white);
  }
  .divider--one { left: 292px; }
  .divider--two { left: 527px; }
  .brand {
    position: absolute;
    left: 0;
    width: 834px;
    top: 392px;
    text-align: center;
    color: var(--lime);
    font-weight: 700;
    font-size: 46px;
    line-height: 50px;
    letter-spacing: 1px;
  }
  .phone {
    position: absolute;
    left: 0;
    width: 834px;
    top: 494px;
    text-align: center;
    color: var(--white);
    font-weight: 700;
    font-size: 118px;
    line-height: 118px;
  }
</style>
</head>
<body>
<div class="canvas">
  <section class="sign">
    <svg class="sign__waves" width="834" height="625" viewBox="0 0 834 625" aria-hidden="true">
      <path d="M0,342 C120,420 250,470 420,472 C600,474 720,400 834,380 L834,625 L0,625 Z" fill="var(--royal)"/>
      <path d="M0,372 C140,440 280,482 440,478 C620,472 730,395 834,368 L834,625 L0,625 Z" fill="var(--white)"/>
      <path d="M0,398 C150,455 300,488 450,484 C620,478 735,405 834,392 L834,625 L0,625 Z" fill="var(--lime)"/>
    </svg>

    <div class="service service--private">
      <span class="service__icon" role="img" aria-label="Private offices icon: desk, chair, lamp and wall frame"></span>
      <p class="service__label">PRIVATE<br>OFFICES</p>
    </div>
    <div class="divider divider--one"></div>
    <div class="service service--virtual">
      <span class="service__icon" role="img" aria-label="Virtual offices icon: reception desk with mail and plant"></span>
      <p class="service__label">VIRTUAL<br>OFFICES</p>
    </div>
    <div class="divider divider--two"></div>
    <div class="service service--lounge">
      <span class="service__icon" role="img" aria-label="Coworking lounge icon: people meeting around a table"></span>
      <p class="service__label">COWORKING<br>LOUNGE</p>
    </div>

    <div class="brand">2417 HARBORVIEW</div>
    <div class="phone">310.555.0142</div>
  </section>
</div>
</body>
</html>
```